Wall Paper / backdrop

I will like to design a wall paper for my Egg Shop.
1: The rider is - Always Fresh
2: I want three primary images on the wall paper
i: small stack of brown egg crates
ii: Broken eggs showing Golden Yoke
iii: Cooked Eggs showing the cooked yoke
Dimension : Width - 4mtrs / Height -1.8mtrs

Target Market(s)

Retail Market

Industry/Entity Type

Retail

Requirements
Must have
• nice creatives , with real life products (eggs)

```html
<!DOCTYPE html>
<html lang="en">
<head>
<meta charset="utf-8">
<title>Always Fresh – Egg Shop Wallpaper</title>
<link rel="stylesheet" href="https://fonts.googleapis.com/css2?family=Dancing+Script:wght@700&display=swap">
<style>
  :root {
    --page-bg: #f2f2f2;
    --board-white: #f1f1f1;
    --board-grey: #e4e4e4;
    --accent-orange: #ee9f1c;
    --ink-black: #111111;
    --line-white: #ffffff;
    --carton-light: #d9cfc2;
    --carton-dark: #a98d74;
    --egg-brown: #cf6d3a;
    --yolk: #f39a12;
    --bowl-rim: #6e4a33;
    --bowl-inner: #c9d5cf;
  }
  * { margin: 0; padding: 0; box-sizing: border-box; }
  html, body {
    width: 1073px;
    height: 1200px;
    overflow: hidden;
    background: var(--page-bg);
  }
  .wallpaper {
    position: absolute;
    left: 0;
    top: 358px;
    width: 1073px;
    height: 483px;
  }
  .wallpaper svg { display: block; width: 100%; height: 100%; }
  .rider {
    font-family: "Dancing Script", cursive;
    font-weight: 700;
  }
  .rider-always { fill: var(--ink-black); }
  .rider-fresh { fill: var(--accent-orange); }
  .accent-band { fill: var(--accent-orange); }
  .accent-line { fill: none; stroke: var(--line-white); stroke-width: 4; }
  .doodle { fill: none; stroke: var(--ink-black); stroke-width: 4; stroke-linecap: round; }
  .icon-dark { fill: var(--ink-black); }
  .icon-orange { fill: var(--accent-orange); }
</style>
</head>
<body>
  <div class="wallpaper">
    <svg viewBox="0 0 1820 820" xmlns="http://www.w3.org/2000/svg">
      <defs>
        <linearGradient id="boardGradient" x1="0" y1="0" x2="1" y2="1">
          <stop offset="0" stop-color="var(--board-white)"/>
          <stop offset="1" stop-color="var(--board-grey)"/>
        </linearGradient>
        <linearGradient id="cartonGradient" x1="0" y1="0" x2="1" y2="0">
          <stop offset="0" stop-color="var(--egg-brown)"/>
          <stop offset="0.5" stop-color="var(--carton-dark)"/>
          <stop offset="1" stop-color="var(--carton-light)"/>
        </linearGradient>
        <radialGradient id="shellGradient">
          <stop offset="0" stop-color="#ffffff"/>
          <stop offset="1" stop-color="#ead9d4"/>
        </radialGradient>
        <radialGradient id="yolkGradient">
          <stop offset="0" stop-color="var(--yolk)"/>
          <stop offset="0.75" stop-color="#f7b53a"/>
          <stop offset="1" stop-color="#f5ede6"/>
        </radialGradient>
        <radialGradient id="bowlGradient">
          <stop offset="0" stop-color="var(--yolk)"/>
          <stop offset="0.3" stop-color="#f6f2ea"/>
          <stop offset="0.6" stop-color="var(--bowl-inner)"/>
          <stop offset="0.9" stop-color="var(--bowl-inner)"/>
          <stop offset="1" stop-color="var(--bowl-rim)"/>
        </radialGradient>
      </defs>

      <rect class="board" width="1820" height="820" fill="url(#boardGradient)"/>

      <g class="corner-band corner-band-top">
        <path class="accent-band" d="M1540,0 L1820,0 L1820,440 L1495,95 Q1465,60 1500,28 Z"/>
        <path class="accent-line" d="M1560,0 Q1512,28 1545,62 L1820,350"/>
      </g>
      <g class="corner-band corner-band-bottom">
        <path class="accent-band" d="M0,415 L225,660 Q262,700 225,740 L150,820 L0,820 Z"/>
        <path class="accent-line" d="M0,478 L185,678 Q212,706 185,736 L100,820"/>
      </g>

      <rect class="egg-crate" role="img" aria-label="Tray of brown eggs in a cardboard crate"
            x="100" y="-180" width="440" height="1100" rx="40"
            fill="url(#cartonGradient)" transform="rotate(-32 320 370)"/>

      <circle class="egg-shell" role="img" aria-label="Broken white eggshell half"
              cx="615" cy="125" r="72" fill="url(#shellGradient)"/>
      <circle class="golden-yolk" role="img" aria-label="Broken egg showing a golden yolk in its shell"
              cx="760" cy="235" r="78" fill="url(#yolkGradient)"/>

      <g class="fried-egg-bowl" role="img" aria-label="Fried egg with cooked yolk in a ceramic bowl">
        <circle cx="1585" cy="550" r="205" fill="url(#bowlGradient)"/>
      </g>

      <g class="icon-thumbs-up">
        <path class="icon-orange" d="M1045,142 L1095,125 L1120,200 L1068,218 Z"/>
        <path class="icon-orange" d="M1100,122 L1120,112 Q1130,80 1125,55 Q1140,45 1150,62 Q1155,88 1145,110 L1195,95 Q1215,95 1212,112 Q1225,125 1212,138 Q1222,152 1205,162 Q1212,178 1192,183 L1130,200 Z"/>
        <circle cx="1102" cy="205" r="6" fill="var(--line-white)"/>
      </g>

      <g class="icon-crown">
        <path class="icon-dark" d="M1540,345 L1545,290 L1565,318 L1585,272 L1605,318 L1625,290 L1630,345 Z"/>
        <circle class="icon-dark" cx="1545" cy="286" r="6"/>
        <circle class="icon-dark" cx="1585" cy="266" r="6"/>
        <circle class="icon-dark" cx="1625" cy="286" r="6"/>
      </g>

      <g class="icon-hearts">
        <path class="icon-dark" d="M440,80 C420,62 418,42 432,38 C442,36 446,44 446,48 C448,42 455,36 465,40 C475,48 462,66 440,80 Z"/>
        <path class="icon-dark" d="M1395,150 C1375,132 1373,112 1387,108 C1397,106 1401,114 1401,118 C1403,112 1410,106 1420,110 C1430,118 1417,136 1395,150 Z"/>
        <path class="icon-dark" d="M1145,705 C1127,688 1125,670 1138,667 C1147,665 1150,672 1150,676 C1152,670 1158,665 1167,669 C1176,676 1164,692 1145,705 Z"/>
      </g>

      <g class="doodles">
        <path class="doodle" d="M750,140 Q790,100 835,78"/>
        <path class="doodle" d="M765,160 Q805,125 850,110"/>
        <path class="doodle" d="M790,168 L840,150"/>
        <path class="doodle" d="M620,650 L630,720"/>
        <path class="doodle" d="M638,645 L652,760"/>
        <path class="doodle" d="M1290,770 L1370,730"/>
        <path class="doodle" d="M1330,780 L1405,745"/>
        <path class="doodle" d="M1370,790 L1410,770"/>
      </g>

      <text class="rider rider-always" x="980" y="470" font-size="250" text-anchor="middle"
            transform="rotate(-25 980 420)">Always</text>
      <text class="rider rider-fresh" x="1165" y="610" font-size="230" text-anchor="middle"
            transform="rotate(-25 1165 560)">Fresh</text>
    </svg>
  </div>
</body>
</html>
```